Computer Service Provider in Need of New Letterhead Design

We are BrackenLoop Computer Services, a computer/IT services company that provides IT Support, software, hardware, virus monitoring, etc. in Vermont. We are looking for new letterhead, that is both professional and matches the current theme of our business cards & website.
Please note that we want to include the following information:
www.BrackenLoop.example
802-471-3926
742 Hollis Meadow Lane, Ashbury Falls, NH 03812
Reliable Support • Friendly Experts • Lasting Results
I will be attaching our logo along with the business card images.
We would love to have the

```html
<!DOCTYPE html>
<html lang="en">
<head>
<meta charset="utf-8">
<title>BrackenLoop Computer Services – Letterhead</title>
<link href="https://fonts.googleapis.com/css2?family=Lato:wght@400;700&family=Tinos:wght@400;700&display=swap" rel="stylesheet">
<style>
  :root {
    --backdrop: #8c8c8c;
    --paper: #f8f8f8;
    --brand-blue: #2a5d8f;
    --accent-orange: #f39223;
    --rule-blue: #5b86b8;
    --ink: #1a1a1a;
    --muted: #555555;
  }
  * { margin: 0; padding: 0; box-sizing: border-box; }
  html, body {
    width: 1200px; height: 1200px; overflow: hidden;
    background: var(--backdrop);
  }
  .letterhead {
    position: absolute; left: 219px; top: 30px;
    width: 762px; height: 1140px;
    background: var(--paper);
    color: var(--ink);
  }
  .brand {
    position: absolute; left: 59px; top: 41px; height: 58px;
    display: flex; align-items: center; gap: 12px;
  }
  .brand-square {
    width: 58px; height: 58px; background: var(--brand-blue);
  }
  .brand-name {
    font-family: "Lato", sans-serif; font-weight: 700;
    font-size: 22px; color: var(--brand-blue); letter-spacing: 0.2px;
    white-space: nowrap;
  }
  .contact {
    position: absolute; right: 56px; top: 56px;
    text-align: right;
    font-family: "Lato", sans-serif; font-size: 14px;
    line-height: 19px; color: var(--muted);
  }
  .header-rule {
    position: absolute; left: 55px; top: 126px;
    width: 650px; height: 4px; background: var(--accent-orange);
  }
  .letter-body {
    position: absolute; left: 69px; top: 232px; width: 624px;
    font-family: "Tinos", serif; font-size: 15px; line-height: 18.6px;
  }
  .letter-body p { text-align: justify; }
  .issue-date { margin-bottom: 55px; }
  .recipient { margin-bottom: 55px; }
  .subject { font-weight: 700; margin-bottom: 55px; }
  .salutation { margin-bottom: 18px; }
  .paragraph { margin-bottom: 18px; }
  .acknowledge { margin-bottom: 56px; }
  sup { font-size: 9px; line-height: 0; }
  .footer-tagline {
    position: absolute; left: 0; right: 0; top: 1052px;
    text-align: center;
    font-family: "Lato", sans-serif; font-size: 15px; color: var(--ink);
  }
  .dot { color: var(--accent-orange); padding: 0 3px; }
  .footer-rule {
    position: absolute; left: 49px; top: 1082px;
    width: 663px; height: 1.5px; background: var(--rule-blue);
  }
  .footer-address {
    position: absolute; left: 0; right: 0; top: 1093px;
    text-align: center;
    font-family: "Lato", sans-serif; font-size: 16px; color: var(--ink);
  }
</style>
</head>
<body>
  <main class="letterhead">
    <header>
      <div class="brand">
        <div class="brand-square"></div>
        <span class="brand-name">BrackenLoop Computer Services</span>
      </div>
      <div class="contact">
        <div>802-471-3926</div>
        <div>www.BrackenLoop.example</div>
      </div>
      <div class="header-rule"></div>
    </header>

    <section class="letter-body">
      <div class="issue-date">Issuing date: May 5, 2012</div>
      <div class="recipient">
        Name of employee: Mr. xyz<br>
        Address of employee<br>
        address line 2
      </div>
      <div class="subject">Ref: Promotion as an Assistant secretary</div>
      <div class="salutation">Dear Mr. xyz,</div>
      <p class="paragraph">I have the pleasure to inform you that you have been promoted as assistant secretary in the share department of the company. You are required to take charge of the new assignment on 15<sup>th</sup> May, 2012. Please accept my hearty congratulations on your promotion.</p>
      <p class="paragraph">Your salary scale in the promoted cadre will be Tk. 16,000 and from 15th may, your basic salary will be fixed at Tk. 12,000 in the said scale. You will be entitled to all other allowances as applicable to the staff-II of the company. Other services conditions remain unchanged.</p>
      <p class="acknowledge">Please acknowledge receipt of this letter.</p>
      <div class="closing">Yours sincerely,</div>
    </section>

    <footer>
      <div class="footer-tagline">Reliable Support<span class="dot">•</span>Friendly Experts<span class="dot">•</span>Lasting Results</div>
      <div class="footer-rule"></div>
      <div class="footer-address">742 Hollis Meadow Lane, Ashbury Falls, NH 03812</div>
    </footer>
  </main>
</body>
</html>
```